Animal Eye Clinic needs a Business card

We are a new veterinary ophthalmology practice (Ridgeline Pet Vision Care) and we need a business card designed. We only see animal eyes - we are not a regular veterinary clinic. We already have a logo. We are looking for a professional, good looking business card to hand out to our clients. We are looking for something simple but professional and contemporary. Our logo is likely the only picture/graphic that needs to be on the card.
Updates

Contact Information for Business Card

Delia Vossman, BSc, DVM, MSc, DipACVO
Veterinary Ophthalmologist

Phone: 250.418.3927
Email: ridgelinepetvisioncare@mailbox-example.net
Website: ridgelinepetvisioncare-example.net
Address: 1874 Thornbury Rd
Kelowna, BC, V1X 4M9

Colors

Designer to choose colors to be used in the design.

Requirements
Must have
• Our logo (attached)

```html
<!DOCTYPE html>
<html lang="en">
<head>
<meta charset="utf-8">
<title>Ridgeline Pet Vision Care — Business Card</title>
<link rel="stylesheet" href="https://fonts.googleapis.com/css2?family=Open+Sans:wght@400;700&display=swap">
<style>
  :root {
    --teal: #0197a8;
    --white: #ffffff;
    --page: #ececec;
    --text-grey: #8c8c8c;
    --edge: #c9c9c9;
  }
  * { margin: 0; padding: 0; box-sizing: border-box; }
  html, body {
    width: 1200px;
    height: 1200px;
    overflow: hidden;
    background: var(--page);
    font-family: "Open Sans", sans-serif;
  }
  .card {
    position: absolute;
    left: 362px;
    width: 475px;
    height: 269px;
    overflow: hidden;
  }
  .card--front {
    top: 220px;
    background: var(--white);
    border: 1px solid var(--edge);
  }
  .card--back {
    top: 711px;
    background: var(--teal);
  }
  .chevron {
    position: absolute;
    inset: 0;
    width: 100%;
    height: 100%;
  }
  .chevron--teal { fill: var(--teal); }
  .chevron--white { fill: var(--white); }

  .brand {
    position: absolute;
    left: 22px;
    top: 104px;
    width: 230px;
    display: flex;
    align-items: center;
    justify-content: flex-end;
    gap: 8px;
  }
  .brand__dot {
    width: 36px;
    height: 36px;
    border-radius: 50%;
    background: var(--teal);
    flex: none;
  }
  .brand__name {
    color: var(--teal);
    font-weight: 700;
    font-size: 15px;
    line-height: 17px;
    text-transform: uppercase;
    text-align: right;
  }
  .person {
    position: absolute;
    left: 22px;
    top: 165px;
    width: 230px;
    text-align: right;
    color: var(--text-grey);
    font-size: 10px;
    line-height: 15px;
  }
  .contact {
    position: absolute;
    left: 0;
    top: 98px;
    width: 248px;
    list-style: none;
    text-align: right;
    color: var(--white);
    font-size: 10px;
    line-height: 16.7px;
  }
</style>
</head>
<body>
  <section class="card card--front" aria-label="Business card front">
    <svg class="chevron chevron--teal" viewBox="0 0 380 215" preserveAspectRatio="none" aria-hidden="true">
      <path d="M305 0 L380 0 Q312 50 283 107.5 Q312 165 380 215 L305 215 Q238 165 210 107.5 Q238 50 305 0 Z"/>
    </svg>
    <div class="brand">
      <span class="brand__dot" aria-hidden="true"></span>
      <p class="brand__name">Ridgeline Pet<br>Vision Care</p>
    </div>
    <div class="person">
      <p class="person__name">Delia Vossman, BSc, DVM, MSc, DipACVO</p>
      <p class="person__title">Veterinary Ophthalmologist</p>
    </div>
  </section>

  <section class="card card--back" aria-label="Business card back">
    <svg class="chevron chevron--white" viewBox="0 0 380 215" preserveAspectRatio="none" aria-hidden="true">
      <path d="M305 0 L380 0 Q312 50 283 107.5 Q312 165 380 215 L305 215 Q238 165 210 107.5 Q238 50 305 0 Z"/>
    </svg>
    <ul class="contact">
      <li>Phone: 250.418.3927</li>
      <li>Email: ridgelinepetvisioncare@mailbox-example.net</li>
      <li>Website: ridgelinepetvisioncare-example.net</li>
      <li>Address: 1874 Thornbury Rd</li>
      <li>Kelowna, BC, V1X 4M9</li>
    </ul>
  </section>
</body>
</html>
```